Banner poster with different motifs

I'm looking for 5 banners and posters in A1 format in the same design, or the similarity must be recognizable...
Kept quite simple with different titles.

1 ballet
2 Contemporary Dance
3 high heels
4 Salsa & Bachata & Zouk
5 Hip Hop

Modern bright colors
it is for the entrance so that the students see here is a dance school

The text may also be included in the image
The photos are for guidance only; some are our own, some are purchased. However, we are permitted to use them, including our logo, of course.

```html
<!DOCTYPE html>
<html lang="en">
<head>
<meta charset="utf-8">
<title>Solvivida Dance Center Frankfurt – Salsa Bachata Zouk</title>
<link rel="stylesheet" href="https://fonts.googleapis.com/css2?family=Roboto:wght@400;700&family=Montserrat:wght@400&display=swap">
<style>
  :root {
    --teal: #21d4dc;
    --sun: #fdbe58;
    --white: #ffffff;
    --shadow: rgba(0, 60, 70, 0.35);
    --photo-dark: #3a3d44;
    --photo-wine: #7a1f2c;
  }
  html, body {
    margin: 0;
    padding: 0;
    width: 1200px;
    height: 847px;
    overflow: hidden;
    background: var(--teal);
  }
  .poster {
    display: block;
    width: 1200px;
    height: 847px;
  }
  .poster__bg { fill: var(--teal); }
  .dot { fill: var(--sun); }
  .brand__ring { fill: none; stroke: var(--white); stroke-width: 1.5; }
  .brand__name {
    font-family: "Montserrat", sans-serif;
    font-weight: 400;
    font-size: 29px;
    fill: var(--white);
    letter-spacing: 1px;
  }
  .brand__tag {
    font-family: "Montserrat", sans-serif;
    font-weight: 400;
    font-size: 7.4px;
    fill: var(--white);
    letter-spacing: 2.6px;
  }
  .headline {
    font-family: "Roboto", sans-serif;
    font-weight: 400;
    font-size: 134px;
    fill: var(--white);
    filter: drop-shadow(4px 5px 4px var(--shadow));
  }
  .styles {
    font-family: "Roboto", sans-serif;
    font-weight: 700;
    font-size: 20px;
    fill: var(--white);
  }
  .footer-line {
    font-family: "Roboto", sans-serif;
    font-weight: 400;
    font-size: 15px;
    fill: var(--white);
  }
</style>
</head>
<body>
<svg class="poster" viewBox="0 0 1200 847" xmlns="http://www.w3.org/2000/svg">
  <defs>
    <linearGradient id="photoTone" x1="0" y1="0" x2="1" y2="1">
      <stop offset="0" stop-color="var(--photo-dark)"/>
      <stop offset="0.55" stop-color="#8a7a70"/>
      <stop offset="1" stop-color="var(--photo-wine)"/>
    </linearGradient>
  </defs>

  <rect class="poster__bg" width="1200" height="847"/>

  <!-- decorative dots -->
  <circle class="dot" cx="363" cy="499" r="290"/>
  <circle class="dot" cx="238" cy="170" r="35"/>
  <circle class="dot" cx="945" cy="182" r="63"/>
  <circle class="dot" cx="860" cy="515" r="43"/>
  <circle class="dot" cx="1008" cy="789" r="120"/>

  <!-- dancing couple photo area -->
  <rect class="photo" x="162" y="191" width="382" height="656" rx="40"
        fill="url(#photoTone)" role="img"
        aria-label="Photo of a couple dancing salsa in close embrace"/>

  <!-- brand -->
  <g class="brand">
    <circle class="brand__ring" cx="599" cy="57" r="30"/>
    <text class="brand__name" x="600" y="117" text-anchor="middle" textLength="160" lengthAdjust="spacingAndGlyphs">SOLVIVIDA</text>
    <text class="brand__tag" x="600" y="129" text-anchor="middle" textLength="160">DANCE CENTER FRANKFURT</text>
  </g>

  <!-- headline -->
  <g class="headline">
    <text x="544" y="296">SALSA</text>
    <text x="544" y="418">BACHATA</text>
    <text x="544" y="541">ZOUK</text>
  </g>

  <!-- class list -->
  <g class="styles">
    <text x="547" y="586" xml:space="preserve">BALLET  /  CONTEMPORARY DANCE  /  HIGH HEELS</text>
    <text x="547" y="615" xml:space="preserve">SALSA &amp; BACHATA &amp; ZOUK  /  HIP HOP</text>
  </g>

  <!-- footer -->
  <text class="footer-line" x="480" y="759" textLength="638" xml:space="preserve">SOLVIVIDA  DANCE  CENTER  FRANKFURT</text>
</svg>
</body>
</html>
```